VELQUINT

1. My company will allow people to buy either stock made or custom scented aromatherapy candles, lotions,soaps,body sprays, and wax melts. As there isn't a company that allows for custom oil scent mixes but me. We are just starting with the candles and the other items will be coming later.

2. My target audience is anyone who would want to buy my product. It isn't really limited due to the nature of the product I will be providing.

3. velquint.com is the domain name (purchased from plorvex.com).

4. So what I really need is the shopping cart function. A fully coded shopping cart that will calculate shipping and sales tax if need be. I need the cart function to be just like every other major retailers shopping cart function. So they can click on an item they want and have it go into a shopping cart for the customer to then be able to go and pay for their goods. I also need help creating single pages for each product. So that each thing we make has a separate page with a description and an add to cart button.

5. I would like the color scheme to follow the logo I made. I would also like the logo top center of first page. I would like the quote " elevate your choices in aromatherapy products"

^. I basically need a checkout just like every other good website. A clear shipping area for them to populate, sales tax calculator, ya know everything a normal checkout has like tressly or dunvexa.com. I also have a vonk account already as well.

```html
<!DOCTYPE html>
<html lang="en">
<head>
<meta charset="utf-8">
<title>Velquint — Aromatherapy Products</title>
<link href="https://fonts.googleapis.com/css2?family=Montserrat:wght@400;500;600;700&display=swap" rel="stylesheet">
<style>
:root{
  --purple:#8d4fd1;
  --purple-deep:#6a3cc4;
  --purple-title:#9a55d2;
  --ink:#222;
  --muted:#555;
  --soft-bg:#f3f3f3;
  --star:#f5a623;
  --white:#fff;
}
*{margin:0;padding:0;box-sizing:border-box}
html,body{width:1200px;height:2967px;overflow:hidden;background:var(--white)}
body{font-family:'Montserrat',sans-serif;color:var(--ink)}
.page{position:relative;width:1200px;height:2967px;overflow:hidden}
.abs{position:absolute}
a{text-decoration:none}

/* hero */
.hero{left:0;top:0;width:1200px;height:518px;background:linear-gradient(100deg,#2e1f33 0%,#5a3f55 30%,#a07f86 60%,#c9b2ae 80%,#7c6461 100%)}
.nav{left:0;top:0;width:1200px;height:104px}
.nav a{position:absolute;top:43px;color:var(--white);font-size:16px}
.nav .active{left:92px;top:36px;padding:6px 16px;border:1px solid #b88ae6;border-radius:6px;font-weight:700;background:rgba(0,0,0,.25)}
.brand{position:absolute;left:530px;top:42px;width:140px;display:flex;align-items:center;gap:6px;justify-content:center}
.brand .dot{display:block;width:12px;height:12px;border-radius:50%;background:#b57be6}
.brand span{color:var(--white);font-weight:700;font-size:16px;letter-spacing:2px}
.hero-title{left:112px;top:184px;width:520px;color:var(--white);font-size:43px;line-height:53px;font-weight:600}
.btn{display:inline-block;background:var(--purple);color:var(--white);border-radius:6px;font-size:15px;font-weight:500;text-align:center}
.hero-btn{left:111px;top:366px;width:118px;height:37px;line-height:37px}

/* titles */
.section-title{left:0;width:1200px;text-align:center;color:var(--purple-title);font-weight:600;font-size:40px}

/* products */
.card{top:683px;width:300px;height:376px;border:1px solid #bbb;border-radius:14px;background:var(--white)}
.card.lifted{box-shadow:0 2px 10px rgba(0,0,0,.15);border-color:#ddd}
.card .photo{position:absolute;left:50px;top:30px;width:200px;height:135px;border-radius:10px}
.card .fav{position:absolute;right:16px;top:13px;width:36px;height:36px;border-radius:50%;background:var(--white);box-shadow:0 1px 5px rgba(0,0,0,.2)}
.card .stars{position:absolute;left:0;top:192px;width:100%;text-align:center}
.card h3{position:absolute;left:0;top:218px;width:100%;text-align:center;color:var(--purple-deep);font-size:22px;font-weight:600}
.card p{position:absolute;left:30px;top:250px;width:240px;text-align:center;font-size:14px;line-height:20px;color:var(--muted)}
.card .price{position:absolute;left:20px;top:315px;font-size:19px;font-weight:600}
.card .btn{position:absolute;right:20px;top:308px;width:118px;height:37px;line-height:37px}
.arrow{width:54px;height:54px}

/* benefits */
.benefits{left:0;top:1145px;width:1200px;height:504px;background:var(--soft-bg)}
.benefit{top:1370px;width:222px;height:138px;background:var(--white);border-radius:14px}
.benefit .ring{position:absolute;left:50%;top:-70px;margin-left:-60px;width:120px;height:120px;border-radius:50%;background:var(--soft-bg)}
.benefit .icon{position:absolute;left:50%;top:-57px;margin-left:-50px;width:100px;height:100px;border-radius:50%;background:var(--purple)}
.benefit h4{position:absolute;left:10px;top:68px;width:202px;text-align:center;color:var(--purple);font-weight:600;font-size:17px;line-height:26px}
.pager{left:496px;top:1558px;display:flex;gap:12px}
.pager i{display:block;width:43px;height:3px;background:#bbb}
.pager i.on{background:var(--purple)}

/* promo */
.promo{left:0;top:1649px;width:1200px;height:471px}
.promo-copy{left:300px;top:1756px;width:600px;text-align:center;color:var(--white)}
.promo-copy h2{font-size:39px;font-weight:600;line-height:47px}
.promo-copy p{margin:34px auto 0;width:440px;font-size:14.5px;line-height:23px}
.promo-btn{left:516px;top:1967px;width:167px;height:37px;line-height:37px;background:#5a2fc2;font-size:14px}

/* testimonials */
.review{top:2280px;width:230px;text-align:center}
.review .avatar{width:95px;height:95px;border-radius:50%;margin:0 auto}
.review .stars{margin-top:12px}
.review p{margin-top:12px;font-size:14px;line-height:19.5px;color:var(--muted)}
.review h5{margin-top:14px;font-size:18px;font-weight:600;color:var(--ink)}

/* footer */
.footer{left:0;top:2643px;width:1200px;height:324px;background:linear-gradient(100deg,#a45ccf,#8a4fd0 50%,#5f3ac0)}
.footer-brand{left:100px;top:2768px;width:140px;display:flex;align-items:center;gap:6px;justify-content:center}
.footer-brand .dot{display:block;width:12px;height:12px;border-radius:50%;background:var(--white)}
.footer-brand span{color:var(--white);font-weight:700;font-size:17px;letter-spacing:2px}
.col{top:2693px;color:var(--white)}
.col h6{font-size:20px;font-weight:600;margin-bottom:16px}
.col li{list-style:none;font-size:15px;line-height:26.5px}
.pay{left:940px;top:2834px;color:var(--white);font-size:26px;font-weight:700}
.divider{left:0;top:2906px;width:1200px;height:1px;background:rgba(255,255,255,.45)}
.copyright{left:0;top:2920px;width:1200px;text-align:center;color:var(--white);font-size:13px}
</style>
</head>
<body>
<svg width="0" height="0" style="position:absolute">
  <defs>
    <symbol id="star" viewBox="0 0 24 24"><path d="M12 2l2.9 6.6 7.1.6-5.4 4.7 1.6 7-6.2-3.8-6.2 3.8 1.6-7L2 9.2l7.1-.6z"/></symbol>
  </defs>
</svg>
<div class="page">

  <!-- hero -->
  <div class="abs hero" role="img" aria-label="Photo of lit pillar candles in soft warm light"></div>
  <nav class="abs nav">
    <a class="active" href="#">Home</a>
    <a href="#" style="left:209px">Aromatherapy Candles</a>
    <a href="#" style="left:435px">Lotions</a>
    <div class="brand"><i class="dot"></i><span>VELQUINT</span></div>
    <a href="#" style="left:710px">Soap</a>
    <a href="#" style="left:797px">Body Sprays</a>
    <a href="#" style="left:940px">Wax Melts</a>
    <svg class="abs" style="left:1056px;top:44px" width="17" height="17" viewBox="0 0 20 20" fill="none" stroke="#fff" stroke-width="2.5"><circle cx="8" cy="8" r="6"/><path d="M12.5 12.5L18 18"/></svg>
    <svg class="abs" style="left:1088px;top:43px" width="18" height="17" viewBox="0 0 20 18" fill="#fff"><path d="M0 1h3l1 2h16l-3 8H6l-1 2h13v2H3l2-4L2 3H0z"/><circle cx="7" cy="16.5" r="1.5"/><circle cx="16" cy="16.5" r="1.5"/></svg>
  </nav>
  <h1 class="abs hero-title">Elevate Your Choices In Aromatherapy Products</h1>
  <a class="abs btn hero-btn" href="#">Shop Now</a>

  <!-- products -->
  <h2 class="abs section-title" style="top:593px">Our Products</h2>
  <svg class="abs arrow" style="left:40px;top:842px" viewBox="0 0 54 54" fill="none" stroke="#111" stroke-width="2"><circle cx="27" cy="27" r="25.5"/><path d="M31 17L21 27l10 10"/></svg>
  <svg class="abs arrow" style="left:1109px;top:842px" viewBox="0 0 54 54" fill="none" stroke="#111" stroke-width="2"><circle cx="27" cy="27" r="25.5"/><path d="M23 17l10 10-10 10"/></svg>

  <div class="abs card lifted" style="left:110px">
    <div class="photo" role="img" aria-label="Pink candle in a tin with its lid" style="background:linear-gradient(90deg,#d8d8d8,#e9c9cc)"></div>
    <svg class="fav" viewBox="0 0 36 36"><path d="M18 26l-6.5-6.3a4.2 4.2 0 016-6l.5.6.5-.6a4.2 4.2 0 016 6z" fill="#7a44d0"/></svg>
    <div class="stars"><svg width="90" height="17" viewBox="0 0 90 17" fill="#f5a623" stroke="#f5a623"><use href="#star" width="16" height="16"/><use href="#star" x="18" width="16" height="16"/><use href="#star" x="36" width="16" height="16"/><use href="#star" x="54" width="16" height="16"/><use href="#star" x="72" width="16" height="16" fill="none" stroke-width="2"/></svg></div>
    <h3>Lorem ipsum dolor sit</h3>
    <p>Lorem ipsum dolor sit consectetur adipiscing elit, sed do</p>
    <span class="price">$59.99</span>
    <a class="btn" href="#">Add To Cart</a>
  </div>

  <div class="abs card" style="left:450px">
    <div class="photo" role="img" aria-label="Candle in an amber glass jar" style="background:linear-gradient(90deg,#f1ece8,#a8683a 40%,#fff 55%,#6b3a1c 80%,#f1ece8)"></div>
    <svg class="fav" viewBox="0 0 36 36"><path d="M18 26l-6.5-6.3a4.2 4.2 0 016-6l.5.6.5-.6a4.2 4.2 0 016 6z" fill="none" stroke="#7a44d0" stroke-width="1.8"/></svg>
    <div class="stars"><svg width="90" height="17" viewBox="0 0 90 17" fill="#f5a623" stroke="#f5a623"><use href="#star" width="16" height="16"/><use href="#star" x="18" width="16" height="16"/><use href="#star" x="36" width="16" height="16"/><use href="#star" x="54" width="16" height="16"/><use href="#star" x="72" width="16" height="16" fill="none" stroke-width="2"/></svg></div>
    <h3>Lorem ipsum dolor sit</h3>
    <p>Lorem ipsum dolor sit consectetur adipiscing elit, sed do</p>
    <span class="price">$59.99</span>
    <a class="btn" href="#">Add To Cart</a>
  </div>

  <div class="abs card" style="left:790px">
    <div class="photo" role="img" aria-label="Boxed candle beside a lit candle jar" style="background:linear-gradient(90deg,#7a5a4e,#c9b3a0 50%,#e5dfd8)"></div>
    <svg class="fav" viewBox="0 0 36 36"><path d="M18 26l-6.5-6.3a4.2 4.2 0 016-6l.5.6.5-.6a4.2 4.2 0 016 6z" fill="none" stroke="#7a44d0" stroke-width="1.8"/></svg>
    <div class="stars"><svg width="90" height="17" viewBox="0 0 90 17" fill="#f5a623" stroke="#f5a623"><use href="#star" width="16" height="16"/><use href="#star" x="18" width="16" height="16"/><use href="#star" x="36" width="16" height="16"/><use href="#star" x="54" width="16" height="16"/><use href="#star" x="72" width="16" height="16" fill="none" stroke-width="2"/></svg></div>
    <h3>Lorem ipsum dolor sit</h3>
    <p>Lorem ipsum dolor sit consectetur adipiscing elit, sed do</p>
    <span class="price">$59.99</span>
    <a class="btn" href="#">Add To Cart</a>
  </div>

  <!-- benefits -->
  <div class="abs benefits"></div>
  <h2 class="abs section-title" style="top:1222px">Our Benefits</h2>

  <div class="abs benefit" style="left:112px">
    <div class="ring"></div>
    <svg class="icon" viewBox="0 0 100 100" fill="#fff"><path d="M28 68c0-22 16-36 44-38-2 26-16 42-38 42z"/><path d="M30 72l28-28" stroke="#8d4fd1" stroke-width="3"/></svg>
    <h4>Natural, High-Quality Ingredients</h4>
  </div>
  <div class="abs benefit" style="left:363px">
    <div class="ring"></div>
    <svg class="icon" viewBox="0 0 100 100" fill="#fff"><rect x="26" y="40" width="12" height="34" rx="2"/><path d="M32 24c4 5 4 9 0 12-4-3-4-7 0-12z"/><path d="M42 62h32v12H42z"/><circle cx="62" cy="46" r="8"/></svg>
    <h4>Aromatherapy Benefits</h4>
  </div>
  <div class="abs benefit" style="left:615px">
    <div class="ring"></div>
    <svg class="icon" viewBox="0 0 100 100" fill="none" stroke="#fff" stroke-width="4"><rect x="42" y="24" width="30" height="52" rx="5"/><path d="M24 42h6l5 14h14M34 64a2 2 0 100 .1M46 64a2 2 0 100 .1"/></svg>
    <h4>Convenient Online Shopping</h4>
  </div>
  <div class="abs benefit" style="left:866px">
    <div class="ring"></div>
    <svg class="icon" viewBox="0 0 100 100" fill="none" stroke="#fff" stroke-width="4"><circle cx="50" cy="50" r="10"/><circle cx="50" cy="50" r="24" stroke-dasharray="8 6"/><path d="M50 20v-4M50 84v-4M20 50h-4M84 50h-4"/></svg>
    <h4>Personalized Scent Blends</h4>
  </div>
  <div class="abs pager"><i></i><i class="on"></i><i></i><i></i></div>

  <!-- promo band -->
  <svg class="abs promo" viewBox="0 0 1200 471" preserveAspectRatio="none" role="img" aria-label="Photos of lit candles framing a purple panel with a faint lotus flower">
    <defs>
      <linearGradient id="leftPhoto" x1="0" x2="1"><stop offset="0" stop-color="#8a6a55"/><stop offset=".5" stop-color="#e8d8c4"/><stop offset="1" stop-color="#b59a84"/></linearGradient>
      <linearGradient id="rightPhoto" x1="0" x2="1"><stop offset="0" stop-color="#6e5446"/><stop offset=".5" stop-color="#b06a2e"/><stop offset="1" stop-color="#3e2c24"/></linearGradient>
      <linearGradient id="panel" x1="0" x2="1"><stop offset="0" stop-color="#a85bd6"/><stop offset="1" stop-color="#6a3ccc"/></linearGradient>
    </defs>
    <rect width="600" height="471" fill="url(#leftPhoto)"/>
    <rect x="600" width="600" height="471" fill="url(#rightPhoto)"/>
    <polygon points="213,0 985,0 762,471 437,471" fill="#fff"/>
    <polygon points="234,0 965,0 751,471 449,471" fill="url(#panel)"/>
  </svg>
  <div class="abs promo-copy">
    <h2>Elevate Your Aromatherapy Experience</h2>
    <p>Lorem ipsum dolor sit amet, consectetur adipiscing elit, sed do eiusmod tempor incididunt ut labore et dolore magna aliqua quis ipsum suspendisse ultrices</p>
  </div>
  <a class="abs btn promo-btn" href="#">Shop Now</a>

  <!-- testimonials -->
  <h2 class="abs section-title" style="top:2197px">Client Testimonials</h2>
  <svg class="abs arrow" style="left:38px;top:2392px" viewBox="0 0 54 54" fill="none" stroke="#111" stroke-width="2"><circle cx="27" cy="27" r="25.5"/><path d="M31 17L21 27l10 10"/></svg>
  <svg class="abs arrow" style="left:1107px;top:2392px" viewBox="0 0 54 54" fill="none" stroke="#111" stroke-width="2"><circle cx="27" cy="27" r="25.5"/><path d="M23 17l10 10-10 10"/></svg>

  <div class="abs review" style="left:107px">
    <div class="avatar" role="img" aria-label="Portrait of John Peter" style="background:linear-gradient(#f2c9a8,#c9916e)"></div>
    <div class="stars"><svg width="90" height="17" viewBox="0 0 90 17" fill="#f5a623" stroke="#f5a623"><use href="#star" width="16" height="16"/><use href="#star" x="18" width="16" height="16"/><use href="#star" x="36" width="16" height="16"/><use href="#star" x="54" width="16" height="16"/><use href="#star" x="72" width="16" height="16" fill="none" stroke-width="2"/></svg></div>
    <p>Lorem ipsum dolor sit consectetur adipiscing elit, sed do eiusmod tempor incididunt ut labore et dolore magna aliqua quis ipsum</p>
    <h5>John Peter</h5>
  </div>
  <div class="abs review" style="left:359px">
    <div class="avatar" role="img" aria-label="Portrait of Henry" style="background:linear-gradient(#9a9590,#6a625a)"></div>
    <div class="stars"><svg width="90" height="17" viewBox="0 0 90 17" fill="#f5a623" stroke="#f5a623"><use href="#star" width="16" height="16"/><use href="#star" x="18" width="16" height="16"/><use href="#star" x="36" width="16" height="16"/><use href="#star" x="54" width="16" height="16"/><use href="#star" x="72" width="16" height="16" fill="none" stroke-width="2"/></svg></div>
    <p>Lorem ipsum dolor sit consectetur adipiscing elit, sed do eiusmod tempor incididunt ut labore et dolore magna aliqua quis ipsum</p>
    <h5>Henry</h5>
  </div>
  <div class="abs review" style="left:612px">
    <div class="avatar" role="img" aria-label="Portrait of Sophia" style="background:linear-gradient(#bfe3e6,#7fc4cc)"></div>
    <div class="stars"><svg width="90" height="17" viewBox="0 0 90 17" fill="#f5a623" stroke="#f5a623"><use href="#star" width="16" height="16"/><use href="#star" x="18" width="16" height="16"/><use href="#star" x="36" width="16" height="16"/><use href="#star" x="54" width="16" height="16"/><use href="#star" x="72" width="16" height="16" fill="none" stroke-width="2"/></svg></div>
    <p>Lorem ipsum dolor sit consectetur adipiscing elit, sed do eiusmod tempor incididunt ut labore et dolore magna aliqua quis ipsum</p>
    <h5>Sophia</h5>
  </div>
  <div class="abs review" style="left:864px">
    <div class="avatar" role="img" aria-label="Portrait of Charlotte" style="background:linear-gradient(#cfcfcf,#9a9a9a)"></div>
    <div class="stars"><svg width="90" height="17" viewBox="0 0 90 17" fill="#f5a623" stroke="#f5a623"><use href="#star" width="16" height="16"/><use href="#star" x="18" width="16" height="16"/><use href="#star" x="36" width="16" height="16"/><use href="#star" x="54" width="16" height="16"/><use href="#star" x="72" width="16" height="16" fill="none" stroke-width="2"/></svg></div>
    <p>Lorem ipsum dolor sit consectetur adipiscing elit, sed do eiusmod tempor incididunt ut labore et dolore magna aliqua quis ipsum</p>
    <h5>Charlotte</h5>
  </div>

  <!-- footer -->
  <footer class="abs footer"></footer>
  <div class="abs footer-brand"><i class="dot"></i><span>VELQUINT</span></div>
  <div class="abs col" style="left:286px"><h6>Quick Links</h6><ul><li>Home</li><li>About Us</li><li>Products</li><li>Testimonails</li><li>Blog</li></ul></div>
  <div class="abs col" style="left:467px"><h6>Our Products</h6><ul><li>Aromatherapy Candles</li><li>Lotions</li><li>Soaps</li><li>Body Spray</li><li>Wax Melts</li></ul></div>
  <div class="abs col" style="left:699px"><h6>Customer Service</h6><ul><li>Contact Us</li><li>Returns &amp; Exchanges</li><li>Shipping &amp; Delivery</li><li>Order Tracking</li><li>FAQ</li></ul></div>
  <div class="abs col" style="left:943px"><h6>Legal Links</h6><ul><li>Privacy Policy</li><li>Cookie Policy</li><li>Terms &amp; Conditions</li></ul></div>
  <div class="abs pay">vonk</div>
  <div class="abs divider"></div>
  <div class="abs copyright">Copyright © 2025 Velquint. All rights reserved.</div>
</div>
</body>
</html>
```